Coastline Premier Retreats Business Card Design

Design a business card for Coastline Premier Retreats. Look at the website for colors and reference. Card should have logo, name, title, office number, mobile number, email, URL and a tagline like, "Luxury Hotel & Resort Email Marketing" (This might change).

https://www.coastlinepremierretreats.example

The rest I will leave up to your imagination.

Contact Information for Business Card

Logo, name, title, office number, mobile number, email, URL and a tagline like, "Luxury Hotel & Resort Email Marketing" (This might change).

```html
<!DOCTYPE html>
<html lang="en">
<head>
<meta charset="utf-8">
<title>Coastline Premier Retreats – Business Card</title>
<link href="https://fonts.googleapis.com/css2?family=Arimo:wght@400;700&display=swap" rel="stylesheet">
<style>
  :root {
    --bg: #d9d9d9;
    --orange: #e46d06;
    --white: #ffffff;
    --ink: #111111;
    --gold: #f2c544;
  }
  * { margin: 0; padding: 0; box-sizing: border-box; }
  html, body { width: 1200px; height: 800px; overflow: hidden; }
  body {
    background: var(--bg);
    font-family: "Arimo", Arial, sans-serif;
    display: flex;
    align-items: center;
    justify-content: center;
    gap: 40px;
  }
  .card {
    position: relative;
    width: 540px;
    height: 310px;
    border-radius: 18px;
    background: var(--orange);
    overflow: hidden;
  }
  .card-front .white-panel {
    position: absolute; inset: 0;
    width: 100%; height: 100%;
  }
  .brand-front {
    position: absolute;
    left: 330px; top: 48px;
    width: 200px;
    text-align: center;
    color: var(--ink);
    font-weight: 700;
    line-height: 1.05;
  }
  .brand-front .brand-main { font-size: 28px; letter-spacing: 1px; }
  .brand-front .brand-sub { font-size: 11px; letter-spacing: 2.5px; margin-top: 4px; }
  .contact-block {
    position: absolute;
    left: 30px; top: 112px;
    color: var(--white);
  }
  .person-name { color: var(--ink); font-weight: 700; font-size: 24px; line-height: 1.15; }
  .person-title { font-size: 15px; margin-top: 2px; }
  .contact-list { list-style: none; margin-top: 12px; font-size: 13px; line-height: 1.45; }
  .contact-list li { display: flex; align-items: center; gap: 8px; }
  .contact-list svg { width: 12px; height: 12px; flex: none; }
  .tagline { font-size: 15px; margin-top: 12px; }
  .card-back {
    display: flex; align-items: center; justify-content: center;
  }
  .brand-back {
    color: var(--gold);
    font-weight: 700;
    text-align: center;
    line-height: 1.05;
  }
  .brand-back .brand-main { font-size: 50px; letter-spacing: 2px; }
  .brand-back .brand-sub { font-size: 19px; letter-spacing: 5px; margin-top: 6px; }
</style>
</head>
<body>

  <section class="card card-front">
    <svg class="white-panel" viewBox="0 0 540 310" aria-hidden="true">
      <polygon points="326,0 540,0 540,92 352,212 326,212" fill="#ffffff"/>
      <polyline points="320,0 320,218 354,218" fill="none" stroke="#111" stroke-width="5"/>
      <line x1="354" y1="218" x2="540" y2="99" stroke="#111" stroke-width="5"/>
    </svg>

    <div class="brand-front">
      <div class="brand-main">COASTLINE</div>
      <div class="brand-sub">PREMIER RETREATS</div>
    </div>

    <div class="contact-block">
      <div class="person-name">Daniel Reeve</div>
      <div class="person-title">President</div>
      <ul class="contact-list">
        <li>
          <svg viewBox="0 0 12 12"><path d="M3 1 L5 3.5 L4 5 Q5 7 7 8 L8.5 7 L11 9 L9.5 11 Q4 10.5 1 3 Z" fill="#111"/></svg>
          555.214.7300
        </li>
        <li>
          <svg viewBox="0 0 12 12"><rect x="3" y="0.5" width="6" height="11" rx="1" fill="none" stroke="#111" stroke-width="1.4"/></svg>
          555.214.7301
        </li>
        <li>
          <svg viewBox="0 0 12 12"><rect x="0.5" y="2" width="11" height="8" fill="#111"/><polyline points="1,2.5 6,6.5 11,2.5" fill="none" stroke="#e46d06" stroke-width="1"/></svg>
          info@coastlinepremierretreats.example
        </li>
        <li>
          <svg viewBox="0 0 12 12"><circle cx="6" cy="6" r="5.5" fill="#111"/><ellipse cx="6" cy="6" rx="2.3" ry="5.5" fill="none" stroke="#e46d06" stroke-width="0.8"/><line x1="0.5" y1="6" x2="11.5" y2="6" stroke="#e46d06" stroke-width="0.8"/></svg>
          www.coastlinepremierretreats.example
        </li>
      </ul>
      <div class="tagline">Luxury Hotel &amp; Resort Email Marketing</div>
    </div>
  </section>

  <section class="card card-back">
    <div class="brand-back">
      <div class="brand-main">COASTLINE</div>
      <div class="brand-sub">PREMIER RETREATS</div>
    </div>
  </section>

</body>
</html>
```